Band and Coaching business card (creative industry)

My company The Fenwick Ensemble is the name of my band Soul outfit but is also a brand I use for my coaching business which is Performance coaching in the following areas: Corporate coaching, acting, vocals and dialect. The band plays for corporate events and private functions as well as local bar/restaurant/festivals.
Updates

Hi All

Please see updated info for the wording of the business card front and back.  This is ito then be followed with contact number, email and facebook link

first side should have:

JulieRose Brannigan
Creative Director
( followed by contact info as per previous)

Side 2:

The Fenwick Ensemble  - Band  
 Vocalist      I   Musician    I  Songwriter

The Fenwick Ensemble  - Studio
Performance Coaching  
Acting  I  Vocals  I Dialect  I Corporate Coaching

Industry/Entity Type

Events

Contact Information for Business Card

The Fenwick Ensemble (logo)
JulieRose Brannigan
Musician/Vocalist/Performance Coach
M: 0412 605 918
E: thefenwickensemble@mailbrook.net
W: www.friendspace.net/thefenwickensembleband

Font styles to use
Sans Serif

Requirements
Must have
• first side should have:

JulieRose Brannigan
Creative Director

Side 2:

The Fenwick Ensemble - Band
Vocalist I Musician I Songwriter

The Fenwick Ensemble - Studio
Performance Coaching
Acting I Vocals I Dialect I Corporate Coaching
Nice to have
• I like smaller business cards with curved edges.

some ideas for look in additional business cards attached.
Should not have
• music notes or anything specific to the field. Want to keep it funky and contemporary

```html
<!DOCTYPE html>
<html lang="en">
<head>
<meta charset="utf-8">
<title>The Fenwick Ensemble – Business Card</title>
<link rel="stylesheet" href="https://fonts.googleapis.com/css2?family=Montserrat:wght@400;600&family=Pacifico&display=swap">
<style>
  :root {
    --backdrop: #e4e4e6;
    --card-white: #ffffff;
    --pink: #d0449a;
    --magenta: #b8409c;
    --purple: #8c3893;
    --plum: #7e2f86;
    --text-pink: #c03f97;
    --name-purple: #86308a;
    --back-text: #ffffff;
  }
  * { margin: 0; padding: 0; box-sizing: border-box; }
  html, body {
    width: 1200px; height: 750px; overflow: hidden;
    background: var(--backdrop);
  }
  .canvas {
    position: relative; width: 1200px; height: 750px;
    display: flex; align-items: center; justify-content: center; gap: 60px;
  }
  .card {
    position: relative; width: 500px; height: 286px;
    border-radius: 30px; overflow: hidden;
    box-shadow: 0 10px 28px rgba(0,0,0,0.16);
  }
  .card-front { background: var(--card-white); }
  .card-front .brand-shape { position: absolute; inset: 0; }
  .brand-mark {
    position: absolute; display: flex; align-items: center; justify-content: center;
    border: 9px solid #fff; border-radius: 50%;
    background: linear-gradient(135deg, var(--purple), var(--pink));
    color: #fff; font-family: "Montserrat", sans-serif; font-weight: 600;
    text-align: center; line-height: 1.15;
  }
  .card-front .brand-mark { left: 86px; top: 101px; width: 96px; height: 96px; font-size: 11px; }
  .holder-name {
    position: absolute; right: 30px; top: 20px;
    font-family: "Pacifico", cursive; font-weight: 400; font-size: 25px; color: var(--name-purple);
    white-space: nowrap;
  }
  .holder-title {
    position: absolute; right: 32px; top: 62px;
    font-family: "Montserrat", sans-serif; font-weight: 600; font-size: 10px; color: var(--name-purple);
    white-space: nowrap;
  }
  .holder-role {
    position: absolute; right: 32px; top: 77px;
    font-family: "Montserrat", sans-serif; font-size: 9px; color: var(--text-pink);
    white-space: nowrap;
  }
  .contact-list {
    position: absolute; left: 232px; top: 112px;
    list-style: none; padding-left: 11px;
    border-left: 1.5px solid var(--text-pink);
    font-family: "Montserrat", sans-serif; font-size: 8.5px; color: var(--text-pink);
    white-space: nowrap;
  }
  .contact-list li { display: flex; align-items: center; gap: 6px; height: 19px; }
  .contact-list svg { width: 10px; height: 10px; flex: none; fill: var(--text-pink); }
  .card-back {
    background: linear-gradient(30deg, var(--pink) 0%, var(--magenta) 45%, var(--plum) 100%);
  }
  .halo {
    position: absolute; left: 195px; top: 20px; width: 110px; height: 110px;
    border-radius: 50%; background: rgba(255,255,255,0.07);
    box-shadow: 0 0 24px rgba(120,30,110,0.25);
  }
  .card-back .brand-mark { left: 209px; top: 34px; width: 82px; height: 82px; font-size: 9.5px; border-width: 7px;
    background: linear-gradient(135deg, var(--pink), var(--magenta)); }
  .services {
    position: absolute; left: 30px; right: 30px; top: 158px;
    display: flex; justify-content: center; gap: 40px;
    font-family: "Montserrat", sans-serif; color: var(--back-text); text-align: center;
  }
  .service-group { display: flex; flex-direction: column; gap: 5px; }
  .service-heading { font-weight: 600; font-size: 10px; }
  .service-sub { font-weight: 600; font-size: 8.5px; opacity: 0.9; }
  .service-list { font-weight: 400; font-size: 8.5px; white-space: nowrap; }
</style>
</head>
<body>
<main class="canvas">
  <section class="card card-front" aria-label="Business card front">
    <svg class="brand-shape" viewBox="0 0 500 286" aria-hidden="true">
      <defs>
        <linearGradient id="frontBand" x1="0" y1="1" x2="1" y2="0">
          <stop offset="0" stop-color="#d0449a"/>
          <stop offset="1" stop-color="#a63d98"/>
        </linearGradient>
        <linearGradient id="frontDisc" x1="0" y1="1" x2="1" y2="0">
          <stop offset="0" stop-color="#b8409c"/>
          <stop offset="1" stop-color="#8c3893"/>
        </linearGradient>
      </defs>
      <path d="M0 70 Q 60 40 105 55 Q 70 150 130 230 Q 170 275 225 286 H0 Z" fill="url(#frontBand)"/>
      <circle cx="134" cy="149" r="76" fill="url(#frontDisc)"/>
      <circle cx="134" cy="149" r="60" fill="#ffffff" opacity="0.06"/>
    </svg>
    <div class="brand-mark">The Fenwick<br>Ensemble</div>
    <h1 class="holder-name">JulieRose Brannigan</h1>
    <p class="holder-title">Creative Director</p>
    <p class="holder-role">Musician/Vocalist/Performance Coach</p>
    <ul class="contact-list">
      <li><svg viewBox="0 0 10 10"><path d="M2 0.5 L3.8 2.6 L2.9 3.6 Q3.8 5.7 6.4 7.1 L7.4 6.2 L9.5 8 L8.2 9.5 Q4 9 0.5 1.8 Z"/></svg>0412 605 918</li>
      <li><svg viewBox="0 0 10 10"><path d="M0.5 2 H9.5 V8 H0.5 Z M1 2.4 L5 5.4 L9 2.4" fill="none" stroke="#c03f97" stroke-width="1"/></svg>thefenwickensemble@mailbrook.net</li>
      <li><svg viewBox="0 0 10 10"><circle cx="5" cy="5" r="4"/></svg>www.friendspace.net/thefenwickensembleband</li>
    </ul>
  </section>

  <section class="card card-back" aria-label="Business card back">
    <div class="halo"></div>
    <div class="brand-mark">The Fenwick<br>Ensemble</div>
    <div class="services">
      <div class="service-group">
        <p class="service-heading">The Fenwick Ensemble – Band</p>
        <p class="service-list">Vocalist&nbsp; | &nbsp;Musician&nbsp; | &nbsp;Songwriter</p>
      </div>
      <div class="service-group">
        <p class="service-heading">The Fenwick Ensemble – Studio</p>
        <p class="service-sub">Performance Coaching</p>
        <p class="service-list">Acting | Vocals | Dialect | Corporate Coaching</p>
      </div>
    </div>
  </section>
</main>
</body>
</html>
```